KORV PTY LTD - Business Cards

Design a modern business card - using the attached Designs.
Same design as on the front, apart from the names/numbers/emails to be different.
We want the cards to be very glossy to stand out, do I think the simple black/white/metallic will be effective.
Both lots of details below:

Tom Wrenshaw
Director
tom_korv@nulvane.com
0438 274 093

Lewis Corbyn
Director
lewis_korv@nulvane.com
0419 385 642

Industry/Entity Type

Business

```html
<!DOCTYPE html>
<html lang="en">
<head>
<meta charset="utf-8">
<title>KORV PTY LTD – Business Cards</title>
<link rel="stylesheet" href="https://fonts.googleapis.com/css2?family=Bitter:wght@700&family=Noto+Sans:wght@400&display=swap">
<style>
  :root {
    --page: #ececec;
    --card-white: #ffffff;
    --card-grey: #b3b3b3;
    --silver-light: #f4f5f6;
    --silver-mid: #c3c8cc;
    --silver-dark: #8f979d;
    --band: #3a3d40;
    --ink: #2e2f31;
    --ink-soft: #444648;
  }
  * { box-sizing: border-box; margin: 0; padding: 0; }
  html, body { width: 1200px; height: 475px; overflow: hidden; background: var(--page); }
  .canvas { position: relative; width: 1200px; height: 475px; }

  .card {
    position: absolute; top: 80px; width: 540px; height: 315px;
    overflow: hidden; box-shadow: 0 6px 18px rgba(0,0,0,.25);
  }
  .card--front { left: 40px; background: var(--card-white); }
  .card--back  { left: 620px; background: var(--card-grey); }

  .card__swoosh { position: absolute; inset: 0; width: 100%; height: 100%; }

  .holder { position: absolute; top: 32px; right: 48px; text-align: right; }
  .holder__name { font: 700 20px/1.1 "Bitter", serif; color: var(--ink); }
  .holder__role { font: 400 13px/1.6 "Noto Sans", sans-serif; color: var(--ink-soft); }

  .brand { position: absolute; display: flex; align-items: center; gap: 12px; }
  .card--front .brand { left: 44px; top: 120px; }
  .card--back .brand { left: 50%; top: 50%; transform: translate(-50%, -50%); }
  .brand__dot { width: 22px; height: 22px; border-radius: 50%; background: var(--band); flex: none; }
  .brand__name { font: 700 44px/1 "Bitter", serif; color: var(--band); letter-spacing: 2px; }
  .brand__sub { display: block; font: 700 11px/1.6 "Bitter", serif; color: var(--band); letter-spacing: 2px; }
  .card--back .brand__name { font-size: 60px; }
  .card--back .brand__sub { font-size: 14px; }
  .card--back .brand__dot { width: 28px; height: 28px; }

  .contact { position: absolute; left: 48px; bottom: 28px; list-style: none; }
  .contact__item { display: flex; align-items: center; gap: 10px; font: 400 14px/1.75 "Noto Sans", sans-serif; color: var(--ink); }
  .contact__icon { width: 12px; height: 12px; fill: var(--ink); flex: none; }
</style>
</head>
<body>
<main class="canvas">

  <section class="card card--front" aria-label="Business card front">
    <svg class="card__swoosh" viewBox="0 0 540 315" preserveAspectRatio="none" aria-hidden="true">
      <defs>
        <linearGradient id="silverSweep" x1="0" y1="0" x2="1" y2="0">
          <stop offset="0" stop-color="var(--silver-light)"/>
          <stop offset="0.35" stop-color="var(--silver-light)"/>
          <stop offset="0.7" stop-color="var(--silver-mid)"/>
          <stop offset="1" stop-color="var(--silver-dark)"/>
        </linearGradient>
      </defs>
      <path d="M0,0 H540 V248 C505,110 310,22 0,26 Z" fill="url(#silverSweep)"/>
      <path d="M0,26 C310,22 505,110 540,248 V300 C495,135 300,40 0,36 Z" fill="var(--band)"/>
    </svg>

    <div class="holder">
      <p class="holder__name">Lewis Corbyn</p>
      <p class="holder__role">Director</p>
    </div>

    <div class="brand">
      <span class="brand__dot"></span>
      <p class="brand__name">KORV<span class="brand__sub">CONTRACTING SERVICES</span></p>
    </div>

    <ul class="contact">
      <li class="contact__item">
        <svg class="contact__icon" viewBox="0 0 24 24" aria-hidden="true"><path d="M6.6 10.8a15 15 0 0 0 6.6 6.6l2.2-2.2a1 1 0 0 1 1-.25 11.4 11.4 0 0 0 3.6.57 1 1 0 0 1 1 1V20a1 1 0 0 1-1 1A17 17 0 0 1 3 4a1 1 0 0 1 1-1h3.5a1 1 0 0 1 1 1c0 1.25.2 2.45.57 3.57a1 1 0 0 1-.25 1z"/></svg>
        0419 385 642
      </li>
      <li class="contact__item">
        <svg class="contact__icon" viewBox="0 0 24 24" aria-hidden="true"><path d="M2 5h20v14H2z M2 5l10 8 10-8" fill="none" stroke="currentColor" stroke-width="0"/><path d="M2 6l10 7 10-7v13H2z"/><path d="M2 4h20l-10 7z"/></svg>
        lewis_korv@nulvane.com
      </li>
    </ul>
  </section>

  <section class="card card--back" aria-label="Business card back">
    <div class="brand">
      <span class="brand__dot"></span>
      <p class="brand__name">KORV<span class="brand__sub">CONTRACTING SERVICES</span></p>
    </div>
  </section>

</main>
</body>
</html>
```